lum-vex needs updated company presentation for perspective principals

We are looking to update our current company overview presentation that we use for giving new and prospective principals (companies we see for) an overview of our company and our capabilities. We have a PowerPoint presentation but would like to give it a more professional and updated look. There are some modification we'd like to incorporate into the new presentation, but that can be added later.
We will also be looking at using this look to update our website and some additional promotion literature for the near future ( Brochures, Mailers....)
Updates

On the territory overview. I need to increase the state view to include Missouri, Iowa, Kansas, Nebraska, Minnesota and Tennessee. This is the first project we've worked on, so please let me know what additional information is required or makes this process go smoother.

Industry/Entity Type

Chemical Product

Font styles to use
Serif

Colors
ec1f27
000000

Requirements
Must have
• Company History, Territory overview, Industries Served, Principal Represented, Employee overview, Historic Performance

```html
<!DOCTYPE html>
<html lang="en">
<head>
<meta charset="utf-8">
<title>lum-vex, inc. — Company Presentation Slides</title>
<link href="https://fonts.googleapis.com/css2?family=Titillium+Web:wght@300;400;700&family=Roboto+Condensed:wght@700&family=Open+Sans:wght@400&display=swap" rel="stylesheet">
<style>
  :root{
    --canvas:#777878;
    --red:#c1121a;
    --red-deep:#3b0608;
    --ink:#1d1d1d;
    --bar:#232323;
    --paper:#f7f7f7;
    --grey-1:#d4d4d8;
    --grey-2:#b4b4b9;
    --grey-3:#6d6d72;
    --icon:#cfcfd3;
    --text-soft:#6a6a6a;
    --cyan:#22c3d6;
    --area:#c0363b;
  }
  *{margin:0;padding:0;box-sizing:border-box}
  html,body{width:1200px;height:1200px;overflow:hidden;background:var(--canvas)}
  body{position:relative;font-family:"Open Sans",sans-serif}
  .slide{position:absolute;width:540px;height:304px;overflow:hidden;background:var(--paper)}
  .s-title{left:51px;top:144px}
  .s-history{left:616px;top:144px}
  .s-territory{left:51px;top:472px}
  .s-industries{left:616px;top:472px}
  .s-options{left:51px;top:801px}
  .s-thanks{left:616px;top:801px}

  .abs{position:absolute}
  .wordmark{font-family:"Titillium Web",sans-serif;font-weight:700;letter-spacing:-0.5px;white-space:nowrap;line-height:1}
  .badge{position:absolute;border-radius:50%;background:#fff;border:3px solid var(--ink)}
  .small{font-size:6px;line-height:1.35;color:var(--text-soft)}

  /* title slide */
  .s-title .dark{position:absolute;left:0;top:0;width:540px;height:232px;background:linear-gradient(135deg,#2a2a2a,#1a1a1a 60%,#222)}
  .s-title .band{position:absolute;left:0;top:232px;width:540px;height:72px;background:var(--red)}
  .s-title .wordmark{left:88px;top:74px;font-size:32px;color:#fff}
  .s-title .tagline{left:88px;top:156px;font-family:"Roboto Condensed",sans-serif;font-weight:700;font-size:17px;color:#fff}
  .s-title .band-text{left:100px;top:248px;width:380px;font-size:6.3px;line-height:1.45;color:#6e0a0e;text-align:center}
  .s-title .badge{left:473px;top:244px;width:52px;height:52px;border-color:var(--red);border-width:4px}

  /* section header */
  .head{position:absolute;left:0;top:0;width:540px;height:51px;background:var(--bar)}
  .head-title{position:absolute;left:30px;top:12px;font-family:"Titillium Web",sans-serif;font-weight:400;font-size:21px;color:#fff}
  .head-num{position:absolute;left:430px;top:0;width:110px;height:51px;background:var(--red);font-family:"Titillium Web",sans-serif;font-weight:300;font-size:28px;color:var(--red-deep);text-align:center;line-height:51px}
  .head .badge{left:383px;top:7px;width:37px;height:37px;border-width:3px}
  .page-mark{position:absolute;left:30px;top:62px;font-size:18px;color:var(--red)}

  /* history */
  .feature{position:absolute;width:110px}
  .feature svg{display:block;height:44px}
  .feature p{margin-top:8px}
  .divider-v{position:absolute;left:337px;top:68px;width:1px;height:217px;background:#d8d8d8}
  .headline{left:362px;top:92px;font-family:"Titillium Web",sans-serif;font-weight:400;font-size:24px;color:var(--ink);line-height:1}
  .headline-sub{left:362px;top:118px;font-size:7.5px;color:#444}
  .para{width:160px;font-size:4.8px;line-height:1.4;color:#555}

  /* territory */
  .steps{position:absolute;left:85px;top:90px;width:370px;height:123px;border-radius:5px;overflow:hidden}
  .step-label{position:absolute;top:26px;font-family:"Titillium Web",sans-serif;font-weight:300;font-size:18px;color:#fff;text-align:center;width:123px}
  .step-text{position:absolute;top:53px;width:100px;font-size:3.6px;line-height:1.45;color:#fff;text-align:center;opacity:.85}
  .territory-text{left:85px;top:232px;width:370px;font-size:6.4px;line-height:1.4;color:#444;text-align:center}

  /* industries */
  .chart{position:absolute;left:0;top:0}
  .legend{position:absolute;top:262px;display:flex;gap:7px;align-items:flex-start}
  .legend i{display:block;width:18px;height:18px;flex:none}
  .legend p{width:90px;font-size:5px;line-height:1.4;color:#555}

  /* options */
  .opt{position:absolute;top:0;width:270px;height:304px;text-align:center}
  .opt-a{left:0;background:var(--red)}
  .opt-b{left:270px;background:#272727}
  .s-options .wordmark{left:49px;top:20px;font-size:20px;color:#fff;text-align:left}
  .opt-title{position:absolute;left:0;width:270px;top:62px;font-family:"Titillium Web",sans-serif;font-weight:400;font-size:30px;letter-spacing:7px;line-height:1}
  .opt-sub{position:absolute;left:0;width:270px;top:92px;font-size:8px}
  .opt-rule{position:absolute;left:101px;top:113px;width:68px;height:1px}
  .opt-body{position:absolute;left:45px;width:180px;top:128px;font-size:5.6px;line-height:1.45}
  .opt-a .opt-title,.opt-a .opt-sub{color:var(--red-deep)}
  .opt-a .opt-rule{background:var(--red-deep)}
  .opt-a .opt-body{color:#7a0a0f}
  .opt-b .opt-title,.opt-b .opt-sub,.opt-b .opt-body{color:#fff}
  .opt-b .opt-rule{background:#777}
  .s-options .badge{left:484px;top:248px;width:37px;height:37px;border-color:#fff;border-width:3px;background:#272727;box-shadow:inset 0 0 0 8px #fff}

  /* thank you */
  .s-thanks{background:linear-gradient(135deg,#1c1c1c,#0d0d0d 55%,#1a1a1a)}
  .centered{position:absolute;left:0;width:540px;text-align:center}
  .s-thanks .wordmark{top:58px;font-size:32px;color:#fff}
  .thank{top:110px;font-family:"Titillium Web",sans-serif;font-weight:300;font-size:44px;line-height:1;color:#fff}
  .you{top:148px;font-family:"Titillium Web",sans-serif;font-weight:300;font-size:44px;line-height:1;color:var(--red)}
  .presenter{top:204px;font-family:"Titillium Web",sans-serif;font-size:9px;color:#fff;letter-spacing:.3px}
  .presenter strong{font-weight:400;font-size:13px}
  .s-thanks .badge{left:251px;top:243px;width:38px;height:38px;border-color:#fff;background:#111;box-shadow:inset 0 0 0 8px #fff}
</style>
</head>
<body>

<!-- Title -->
<section class="slide s-title">
  <div class="dark"></div>
  <div class="band"></div>
  <div class="abs wordmark">lum-vex, inc.</div>
  <div class="abs tagline">Representing the World's Best</div>
  <p class="abs band-text">Lorem ipsum dolor sit amet, ius exerci corpora eu. Per ne meis vocent iudicabit, in oratio graeci atomorum vim, vide habemus docendi ut eam. Cu dolor salutatus efficiendi nam. Debet quaeque nec te. Omittam reprehendunt eu mea, vocent aperiri eum et, ut ius summo dignissim. Pro ne ubique voluptaria, te alia lorem perfecto vix.</p>
  <div class="badge" aria-label="Certification seal"></div>
</section>

<!-- Company History -->
<section class="slide s-history">
  <header class="head">
    <h2 class="head-title">Company History</h2>
    <div class="badge"></div>
    <div class="head-num">01</div>
  </header>
  <div class="wordmark page-mark">lum-vex, inc.</div>

  <div class="feature" style="left:42px;top:88px">
    <svg viewBox="0 0 42 44" width="42"><g fill="var(--icon)"><rect x="0" y="22" width="10" height="22"/><rect x="15" y="12" width="10" height="32"/><rect x="30" y="0" width="12" height="44"/></g></svg>
    <p class="small">Lorem ipsum dolor sit amet, dicit melius consetetur ut eum, vim probo libris dicunt at.</p>
  </div>
  <div class="feature" style="left:177px;top:88px">
    <svg viewBox="0 0 44 44" width="44"><g fill="var(--icon)"><circle cx="22" cy="22" r="15"/><g><rect x="18" y="0" width="8" height="10"/><rect x="18" y="34" width="8" height="10"/><rect x="0" y="18" width="10" height="8"/><rect x="34" y="18" width="10" height="8"/><rect x="18" y="0" width="8" height="10" transform="rotate(45 22 22)"/><rect x="18" y="34" width="8" height="10" transform="rotate(45 22 22)"/><rect x="0" y="18" width="10" height="8" transform="rotate(45 22 22)"/><rect x="34" y="18" width="10" height="8" transform="rotate(45 22 22)"/></g></g><circle cx="22" cy="22" r="7" fill="var(--paper)"/></svg>
    <p class="small">Lorem ipsum dolor sit amet, dicit melius consetetur ut eum, vim probo libris dicunt at.</p>
  </div>
  <div class="feature" style="left:44px;top:190px">
    <svg viewBox="0 0 48 44" width="48"><g fill="var(--icon)"><circle cx="24" cy="12" r="12"/><path d="M0 44 C0 30 10 24 24 24 C38 24 48 30 48 44 Z"/></g></svg>
    <p class="small">Lorem ipsum dolor sit amet, dicit melius consetetur ut eum, vim probo libris dicunt at.</p>
  </div>
  <div class="feature" style="left:177px;top:190px">
    <svg viewBox="0 0 44 44" width="44"><g fill="none" stroke="var(--icon)"><circle cx="17" cy="17" r="13" stroke-width="6"/><path d="M27 27 L41 41" stroke-width="8" stroke-linecap="round"/></g></svg>
    <p class="small">Lorem ipsum dolor sit amet, dicit melius consetetur ut eum, vim probo libris dicunt at.</p>
  </div>

  <div class="divider-v"></div>
  <h3 class="abs headline">HEADLINE</h3>
  <p class="abs headline-sub">Lorem Ipsum Dolor Sit Amet</p>
  <p class="abs para" style="left:362px;top:150px">Lorem ipsum dolor sit amet, ius exerci corpora eu. Per ne meis vocent iudicabit, in oratio graeci atomorum vim, vide habemus docendi ut eam. Cu dolor salutatus efficiendi nam. Debet quaeque nec te. Omittam reprehendunt eu mea, vocent aperiri eum et, ut ius summo dignissim. Pro ne ubique voluptaria, te alia lorem perfecto vix.</p>
  <p class="abs para" style="left:362px;top:201px">Nam dolor latine ornatus id, choro partiendo mei et. Idque facer vidisse id nec, constituam dissentiunt per ex. In nam elitr assueverit, eum te nemore mentitum hendrerit. Eu solum debet minimum qui. Maluisset gloriatur ne eam, usu et dolor clita adversarium. Ex postea petentium comprehensam vel, vim te eligendi intellegat.</p>
</section>

<!-- Territory overview -->
<section class="slide s-territory">
  <header class="head">
    <h2 class="head-title">Territory overview</h2>
    <div class="badge"></div>
    <div class="head-num">02</div>
  </header>
  <div class="wordmark page-mark">lum-vex, inc.</div>

  <div class="steps">
    <svg width="370" height="123" viewBox="0 0 370 123" class="abs" style="left:0;top:0">
      <rect width="370" height="123" fill="var(--grey-3)"/>
      <path d="M0 0 H247 V55 L252 61 L247 67 V123 H0 Z" fill="var(--grey-2)"/>
      <path d="M0 0 H123 V55 L128 61 L123 67 V123 H0 Z" fill="var(--grey-1)"/>
    </svg>
    <div class="step-label" style="left:0">STEP 1</div>
    <div class="step-label" style="left:123px">STEP 2</div>
    <div class="step-label" style="left:247px">STEP 3</div>
    <p class="step-text" style="left:12px">Key states across the central region, with steady growth in new markets and accounts served by local reps each year.</p>
    <p class="step-text" style="left:135px">Expanded coverage now adds new states to the west, with field teams placed close to plants and major buyers there.</p>
    <p class="step-text" style="left:259px">Full regional reach lets each principal count on one team for sales, service and support in every state we cover.</p>
  </div>
  <p class="abs territory-text">Lorem ipsum dolor sit amet, ius exerci corpora eu. Per ne meis vocent iudicabit, in oratio graeci atomorum vim, vide habemus docendi ut eam. Cu dolor salutatus efficiendi nam. Debet quaeque nec te. Omittam reprehendunt eu mea, vocent aperiri eum et, ut ius summo dignissim. Pro ne ubique voluptaria, te alia lorem perfecto vix.</p>
</section>

<!-- Industries Served -->
<section class="slide s-industries">
  <header class="head">
    <h2 class="head-title">Industries Served</h2>
    <div class="badge"></div>
    <div class="head-num">03</div>
  </header>
  <div class="wordmark page-mark">lum-vex, inc.</div>

  <svg class="chart" width="540" height="304" viewBox="0 0 540 304" font-family="Open Sans, sans-serif" font-size="7" fill="#333">
    <g stroke="#cfcfcf" stroke-width=".6" stroke-dasharray="2 2">
      <line x1="84" y1="88" x2="478" y2="88"/><line x1="84" y1="119" x2="478" y2="119"/>
      <line x1="84" y1="150" x2="478" y2="150"/><line x1="84" y1="181" x2="478" y2="181"/>
      <line x1="84" y1="84" x2="84" y2="214"/><line x1="120" y1="84" x2="120" y2="214"/>
      <line x1="156" y1="84" x2="156" y2="214"/><line x1="191" y1="84" x2="191" y2="214"/>
      <line x1="227" y1="84" x2="227" y2="214"/><line x1="263" y1="84" x2="263" y2="214"/>
      <line x1="299" y1="84" x2="299" y2="214"/><line x1="335" y1="84" x2="335" y2="214"/>
      <line x1="370" y1="84" x2="370" y2="214"/><line x1="406" y1="84" x2="406" y2="214"/>
      <line x1="442" y1="84" x2="442" y2="214"/><line x1="478" y1="84" x2="478" y2="214"/>
    </g>
    <g text-anchor="end"><text x="79" y="90">400</text><text x="79" y="121">300</text><text x="79" y="152">200</text><text x="79" y="183">100</text></g>
    <path d="M84 168 L120 146 L156 163 L191 150 L227 140 L263 160 L299 168 L335 158 L370 141 L406 121 L442 133 L478 110 L478 214 L84 214 Z" fill="var(--area)"/>
    <g fill="#777"><circle cx="156" cy="163" r="2.5"/><circle cx="299" cy="168" r="2.5"/><circle cx="406" cy="121" r="2.5"/></g>
    <path d="M138 126 H174 V145 H160 L156 151 L152 145 H138 Z" fill="var(--cyan)"/>
    <path d="M281 132 H317 V151 H303 L299 157 L295 151 H281 Z" fill="#e2484d"/>
    <path d="M388 83 H424 V102 H410 L406 108 L402 102 H388 Z" fill="#e0e0e3"/>
    <g text-anchor="middle"><text x="84" y="226">A</text><text x="120" y="226">B</text><text x="156" y="226">C</text><text x="191" y="226">D</text><text x="227" y="226">E</text><text x="263" y="226">F</text><text x="299" y="226">G</text><text x="335" y="226">H</text><text x="370" y="226">I</text><text x="406" y="226">J</text><text x="442" y="226">K</text><text x="478" y="226">L</text></g>
  </svg>

  <div class="legend" style="left:81px"><i style="background:var(--cyan)"></i><p>Lorem ipsum dolor sit amet, dicit melius consetetur ut eum, vim probo libris dicunt at.</p></div>
  <div class="legend" style="left:215px"><i style="background:#e2484d"></i><p>Lorem ipsum dolor sit amet, dicit melius consetetur ut eum, vim probo libris dicunt at.</p></div>
  <div class="legend" style="left:349px"><i style="background:#e0e0e3"></i><p>Lorem ipsum dolor sit amet, dicit melius consetetur ut eum, vim probo libris dicunt at.</p></div>
</section>

<!-- Options -->
<section class="slide s-options">
  <div class="opt opt-a">
    <h2 class="opt-title">OPTION A</h2>
    <p class="opt-sub">Lorem Ipsum Dolor Sit Amet</p>
    <div class="opt-rule"></div>
    <div class="opt-body">
      <p>Lorem ipsum dolor sit amet, ius exerci corpora eu. Per ne meis vocent iudicabit, in oratio graeci atomorum vim, vide habemus docendi ut eam. Cu dolor salutatus efficiendi nam. Debet quaeque nec te. Omittam reprehendunt eu mea, vocent aperiri eum et, ut ius summo dignissim. Pro ne ubique voluptaria, te alia lorem perfecto vix.</p>
      <p style="margin-top:7px">Nam dolor latine ornatus id, choro partiendo mei et. Idque facer vidisse id nec, constituam dissentiunt per ex. In nam elitr assueverit, eum te nemore mentitum hendrerit. Eu solum debet minimum qui. Maluisset gloriatur ne eam, usu et dolor clita adversarium. Ex postea petentium comprehensam vel, vim te eligendi intellegat.</p>
    </div>
  </div>
  <div class="opt opt-b">
    <h2 class="opt-title">OPTION B</h2>
    <p class="opt-sub">Lorem Ipsum Dolor Sit Amet</p>
    <div class="opt-rule"></div>
    <div class="opt-body">
      <p>Lorem ipsum dolor sit amet, ius exerci corpora eu. Per ne meis vocent iudicabit, in oratio graeci atomorum vim, vide habemus docendi ut eam. Cu dolor salutatus efficiendi nam. Debet quaeque nec te. Omittam reprehendunt eu mea, vocent aperiri eum et, ut ius summo dignissim. Pro ne ubique voluptaria, te alia lorem perfecto vix.</p>
      <p style="margin-top:7px">Nam dolor latine ornatus id, choro partiendo mei et. Idque facer vidisse id nec, constituam dissentiunt per ex. In nam elitr assueverit, eum te nemore mentitum hendrerit. Eu solum debet minimum qui. Maluisset gloriatur ne eam, usu et dolor clita adversarium. Ex postea petentium comprehensam vel, vim te eligendi intellegat.</p>
    </div>
  </div>
  <div class="abs wordmark">lum-vex, inc.</div>
  <div class="badge"></div>
</section>

<!-- Thank you -->
<section class="slide s-thanks">
  <div class="centered wordmark">lum-vex, inc.</div>
  <div class="centered thank">THANK</div>
  <div class="centered you">YOU</div>
  <div class="centered presenter">PRESENTED BY <strong>ALEX</strong></div>
  <div class="badge"></div>
</section>

</body>
</html>
```